I am looking for a modern, clean and neat design for a reflexology and well being business. The business name is Gralo Tund (this is an old Latin word for wellbeing). The colours I would like are purple, white and grey. I am open to suggestions for pictures such as healing or working hands, a pair of feet, images that represent my business that you may think of....... or maybe you think no images at all would be best? My tag line is: "Relax, Renew, Revive" or "Find you balance......... Relax, Renew, Revive" I can decide which I want so I would like to see what both would look like. I would like space on the back to write the client's appointment date and time (more than once)

```html
<!DOCTYPE html>
<html lang="en">
<head>
<meta charset="utf-8">
<title>Gralo Tund – Business Card</title>
<link rel="stylesheet" href="https://fonts.googleapis.com/css2?family=Open+Sans:wght@400;600;700&display=swap">
<style>
  :root {
    --stage: #000000;
    --card: #ffffff;
    --purple: #a000b4;
    --purple-deep: #9400a8;
    --grey: #444444;
    --ink: #1f1f1f;
    --dots: #333333;
  }
  * { box-sizing: border-box; margin: 0; padding: 0; }
  html, body { width: 1200px; height: 900px; overflow: hidden; background: var(--stage); }
  body { position: relative; font-family: "Open Sans", Arial, sans-serif; color: var(--ink); }

  .card { position: absolute; overflow: hidden; }

  /* Front */
  .card-front {
    left: 116px; top: 275px; width: 477px; height: 293px;
    background: var(--card);
    border-radius: 0 56px 0 56px;
  }
  .brand-dot {
    position: absolute; left: 38px; top: 44px;
    width: 44px; height: 44px; border-radius: 50%;
    background: var(--purple);
  }
  .brand-name {
    position: absolute; left: 32px; top: 118px; white-space: nowrap;
    font-size: 40px; line-height: 54px; font-weight: 400; color: var(--grey); letter-spacing: 0.3px;
  }
  .tagline {
    position: absolute; left: 36px; top: 176px; white-space: nowrap;
    font-size: 13px; line-height: 18px; font-weight: 600; color: var(--purple); letter-spacing: 0.3px;
  }
  .person { position: absolute; right: 19px; top: 34px; text-align: right; }
  .person-name { font-size: 19px; font-weight: 700; color: var(--purple); line-height: 24px; }
  .person-role { font-size: 13px; line-height: 18px; }
  .address { position: absolute; right: 21px; top: 156px; text-align: right; font-size: 13px; line-height: 17px; font-style: normal; }
  .contacts { position: absolute; right: 19px; top: 216px; list-style: none; font-size: 13px; line-height: 17.5px; }
  .contacts li { display: flex; justify-content: flex-end; align-items: center; gap: 7px; }
  .contacts svg { width: 10px; height: 10px; fill: var(--purple); }

  /* Back */
  .card-back {
    left: 622px; top: 276px; width: 477px; height: 292px;
    background: var(--card);
    border-radius: 56px 0 56px 0;
  }
  .band { position: absolute; left: 0; width: 100%; background: var(--purple); color: #fff; text-align: center; }
  .band-top { top: 0; height: 79px; }
  .band-bottom { bottom: 0; height: 86px; background: var(--purple-deep); }
  .band-top h2 { font-size: 19px; font-weight: 600; line-height: 92px; }
  .notice { padding-top: 26px; font-size: 14px; font-weight: 600; line-height: 22px; text-transform: uppercase; letter-spacing: 0.2px; }
  .field-row { position: absolute; left: 73px; display: flex; align-items: baseline; font-size: 14px; line-height: 19px; font-weight: 600; color: var(--purple); white-space: nowrap; }
  .row-name { top: 96px; }
  .row-when-1 { top: 134px; }
  .row-when-2 { top: 170px; }
  .leader { display: inline-block; border-bottom: 2px dotted var(--dots); height: 1px; margin: 0 5px; transform: translateY(-2px); }
  .leader-long { width: 296px; }
  .leader-date { width: 104px; margin-right: 10px; }
  .leader-time { width: 92px; }
  .ampm { font-weight: 400; }
</style>
</head>
<body>

<section class="card card-front" aria-label="Business card front">
  <span class="brand-dot"></span>
  <p class="brand-name">Gralo Tund</p>
  <p class="tagline">Relax, Renew, Revive</p>

  <div class="person">
    <p class="person-name">Marcus Ellery</p>
    <p class="person-role">Managing Director</p>
  </div>

  <address class="address">
    12345, Address Goes Here<br>
    Country Name, 123456
  </address>

  <ul class="contacts">
    <li>044-123 456 789
      <svg viewBox="0 0 24 24" aria-hidden="true"><path d="M6.6 10.8a15.1 15.1 0 0 0 6.6 6.6l2.2-2.2a1 1 0 0 1 1-.25 11.4 11.4 0 0 0 3.6.57 1 1 0 0 1 1 1V20a1 1 0 0 1-1 1A17 17 0 0 1 3 4a1 1 0 0 1 1-1h3.5a1 1 0 0 1 1 1c0 1.25.2 2.45.57 3.6a1 1 0 0 1-.25 1z"/></svg>
    </li>
    <li>info@webname.com
      <svg viewBox="0 0 24 24" aria-hidden="true"><path d="M2 5h20v14H2z"/><path d="M3 6l9 6.3L21 6" fill="none" stroke="#fff" stroke-width="2"/></svg>
    </li>
    <li>www.websitename.com
      <svg viewBox="0 0 24 24" aria-hidden="true"><path d="M10 14a4 4 0 0 0 5.7 0l4-4a4 4 0 0 0-5.7-5.7l-1.5 1.5M14 10a4 4 0 0 0-5.7 0l-4 4a4 4 0 0 0 5.7 5.7l1.5-1.5" fill="none" stroke="var(--purple)" stroke-width="2.6" stroke-linecap="round"/></svg>
    </li>
  </ul>
</section>

<section class="card card-back" aria-label="Business card back, appointment card">
  <div class="band band-top"><h2>Your Next Appointment on</h2></div>

  <div class="field-row row-name">Name :<span class="leader leader-long"></span></div>
  <div class="field-row row-when-1">
    Date :<span class="leader leader-date"></span>
    Time :<span class="leader leader-time"></span><span class="ampm">AM / PM</span>
  </div>
  <div class="field-row row-when-2">
    Date :<span class="leader leader-date"></span>
    Time :<span class="leader leader-time"></span><span class="ampm">AM / PM</span>
  </div>

  <div class="band band-bottom">
    <p class="notice">If unable to keep appointment,<br>kindly give 24hrs notice.</p>
  </div>
</section>

</body>
</html>
```